I want a website to be designed for our new company, it's an import and export company for variety of things.

please see the attached Logo for our company and the Images for our different sections for our busienss

Target Market(s)

multiple

Coding

Coded - Design and coding required

Number of Pages Required

5+ page

Font styles to use
Sans Serif

Colors

Designer to choose colors to be used in the design.

Requirements
Must have
• KVR GLOBALINKS
• KVR globalinks Trading & Contracting provides various services. The Company offers infrastructure construction, oil, enegy and gas services, agricultural projects, real estate development, travel and tourism, and food processing and trading.
• Civil contracting for infrastructure, residential and heavy projects. Through its main subsidiaries; distribution of general food products, construction chemicals including corrosion inhibitors and electrical machinery; provides catering and travel agency services; ownership and operation of a school; offers human sources services including manpower supply.
• Drilling and Gold Mines Used Machinery, All Kinds of Construction Machinery, Drilling Machines are manufactured and sold.
Nice to have
• good designa and beautiful colours, it has too look professional

```html
<!DOCTYPE html>
<html lang="en">
<head>
<meta charset="utf-8">
<title>KVR Globalinks — Import &amp; Export</title>
<link href="https://fonts.googleapis.com/css2?family=Poppins:wght@300;400;500;600&family=Roboto+Condensed:wght@400;500;700&display=swap" rel="stylesheet">
<style>
:root{
  --ink:#111111;
  --gold:#cfa64f;
  --green:#85b26a;
  --navy:#1b2152;
  --paper:#ffffff;
  --muted:#444444;
  --offer-cream:#f1e3c6;
  --offer-green:#86b46c;
}
*{margin:0;padding:0;box-sizing:border-box}
html,body{width:1200px;height:3348px;overflow:hidden}
body{position:relative;background:var(--paper);font-family:"Poppins",sans-serif;color:var(--ink)}
.abs{position:absolute}
.cond{font-family:"Roboto Condensed",sans-serif}

/* header */
.site-header{left:0;top:0;width:1200px;height:146px;background:var(--ink);border-bottom:2px solid #e8e8e8}
.brand{left:110px;top:46px;display:flex;align-items:center;gap:12px;color:#fff;font-size:22px;font-weight:500;letter-spacing:3px}
.brand-dot{width:22px;height:22px;border-radius:50%;background:var(--gold)}
.top-contact{top:24px;display:flex;align-items:center;gap:10px;color:#fff;font-size:18px;font-weight:300;white-space:nowrap}
.ring{width:40px;height:40px;border:2px solid #fff;border-radius:50%;display:flex;align-items:center;justify-content:center;flex:none}
.main-nav{top:90px;left:473px;color:#fff;font-size:18px;font-weight:300}
.main-nav span{position:absolute;white-space:nowrap}

/* hero */
.hero-photo{left:0;top:148px;width:1200px;height:620px;background:linear-gradient(110deg,#cfd3d6 0%,#a9aeb1 35%,#6f6a62 60%,#3e3a36 100%)}
.hero-title{right:112px;top:322px;color:#fff;font-size:64px;font-weight:700;letter-spacing:1px;line-height:1;white-space:nowrap}
.hero-sub{right:112px;top:412px;color:#fff;font-size:31px;text-align:right;line-height:42px}
.dots{left:552px;top:687px;display:flex;gap:6px}
.dots i{width:15px;height:15px;border-radius:50%;background:#fff;opacity:.85}

/* service panels */
.service{color:#fff}
.service h2{font-family:"Roboto Condensed",sans-serif;font-weight:500;font-size:31px}
.service p{font-size:14px;font-weight:300;line-height:24px;margin-top:14px}
.btn-outline{display:inline-block;border:2px solid #fff;color:#fff;font-family:"Roboto Condensed",sans-serif;font-size:17px;padding:11px 16px;margin-top:24px}

/* about */
.about{left:0;width:1200px;top:1150px;text-align:center}
.about .eyebrow{font-size:21px;font-weight:500;font-family:"Roboto Condensed",sans-serif}
.about h2{font-family:"Roboto Condensed",sans-serif;font-weight:500;font-size:35px;margin-top:4px}
.about p{width:980px;margin:28px auto 0;font-size:14px;color:var(--muted);font-weight:300;line-height:26px}
.btn-dark{display:inline-block;background:#222;color:#fff;font-family:"Roboto Condensed",sans-serif;font-size:19px;padding:17px 16px;width:117px;margin-top:40px}

/* offers */
.offers-bg{left:0;top:1502px;width:1200px;height:736px;background:linear-gradient(180deg,#ffffff 0%,#eff1f0 30%,#e8ebe9 70%,#ffffff 100%)}
.offers-title{left:0;width:1200px;top:1592px;text-align:center;color:var(--navy);font-family:"Roboto Condensed",sans-serif;font-size:31px;font-weight:500}
.offers-rule{left:567px;top:1652px;width:66px;height:3px;background:var(--ink)}
.tile{display:flex;flex-direction:column;align-items:center;justify-content:center;gap:14px;font-family:"Roboto Condensed",sans-serif;font-size:22px;border-top:4px solid var(--green)}
.tile.cream{background:var(--offer-cream);color:#222}
.tile.green{background:var(--offer-green);color:#fff}
.feature{left:300px;top:1719px;width:598px;height:332px;background:rgba(120,175,98,.92);border-top:6px solid #cfd4cf;color:#fff;text-align:center}
.feature h3{font-family:"Roboto Condensed",sans-serif;font-size:33px;font-weight:500;margin-top:14px}
.feature p{font-size:19px;font-weight:300;line-height:32px;margin-top:10px}

/* projects */
.project{top:2323px;height:375px;width:488px;box-shadow:0 4px 10px rgba(0,0,0,.15)}
.project-photo{position:absolute;left:17px;top:24px;width:190px;height:327px;border:2px solid #fff}
.project-body{position:absolute;left:225px;top:50px;width:250px;color:#fff}
.project-body h3{font-family:"Roboto Condensed",sans-serif;font-size:29px;font-weight:400;line-height:35px}
.project-body p{font-size:15px;font-weight:300;line-height:24px;margin-top:22px}
.btn-white{display:inline-block;background:#fff;font-family:"Roboto Condensed",sans-serif;font-size:18px;padding:18px 14px;margin-top:28px}

/* find band */
.find-band{left:0;top:2786px;width:1200px;height:90px;background:var(--ink)}
.find-title{left:110px;top:2810px;color:#fff;font-size:30px;font-weight:600}
.find-text{left:417px;top:2810px;width:500px;color:#fff;font-size:15px;line-height:25px}
.btn-gold{left:957px;top:2803px;width:130px;height:57px;background:var(--gold);color:#fff;font-family:"Roboto Condensed",sans-serif;font-size:20px;display:flex;align-items:center;justify-content:center}

/* footer */
.site-footer{left:0;top:2878px;width:1200px;height:410px;background:var(--ink)}
.footer-brand{left:118px;top:3075px;color:#fff;font-size:38px;letter-spacing:4px;font-weight:400;display:flex;align-items:center;gap:16px}
.footer-brand .brand-dot{width:30px;height:30px}
.footer-title{left:652px;top:2958px;color:#fff;font-family:"Roboto Condensed",sans-serif;font-size:34px;font-weight:500}
.contact-item{left:649px;display:flex;align-items:center;gap:10px;color:#fff;font-size:22px;line-height:27px}
.contact-item .ring{width:49px;height:49px}
.copyright{left:0;top:3304px;width:1200px;text-align:center;font-size:15px;color:#333}
</style>
</head>
<body>

<header class="abs site-header">
  <div class="abs brand"><span class="brand-dot"></span>KVR GLOBALINKS</div>
  <div class="abs top-contact" style="left:578px">
    <span class="ring"><svg width="20" height="20" viewBox="0 0 24 24" fill="none" stroke="#fff" stroke-width="2"><path d="M5 3h4l2 5-3 2a11 11 0 0 0 6 6l2-3 5 2v4a2 2 0 0 1-2 2A17 17 0 0 1 3 5a2 2 0 0 1 2-2z"/></svg></span>
    +1 555 019 4432
  </div>
  <div class="abs top-contact" style="left:786px">
    <span class="ring"><svg width="20" height="20" viewBox="0 0 24 24" fill="none" stroke="#fff" stroke-width="2"><rect x="3" y="5" width="18" height="14" rx="2"/><path d="M3 7l9 6 9-6"/></svg></span>
    info@kvrglobalinks.com
  </div>
  <nav class="abs main-nav">
    <span style="left:0">Home</span>
    <span style="left:77px">About Us</span>
    <span style="left:177px">Our Services</span>
    <span style="left:304px">Blog</span>
    <span style="left:368px">Gallery</span>
    <span style="left:454px">News</span>
    <span style="left:525px">Contact Us</span>
  </nav>
</header>

<div class="abs hero-photo" role="img" aria-label="Worker in protective clothing filling jars on a food production line"></div>
<h1 class="abs hero-title cond">KVR GLOBALINKS</h1>
<p class="abs hero-sub cond">We are an import and export company<br>for a variety of things.</p>

<svg class="abs" style="left:0;top:630px" width="1200" height="530" viewBox="0 630 1200 530">
  <polygon points="0,638 600,746 1200,638 1200,658 600,768 0,658" fill="#fff"/>
  <polyline points="0,640 600,748 1200,640" fill="none" stroke="#333" stroke-width="2"/>
  <polygon points="0,656 600,768 600,1036 0,1148" fill="var(--gold)"/>
  <polygon points="600,768 1200,656 1200,1148 600,1036" fill="var(--green)"/>
</svg>
<div class="abs dots"><i></i><i></i><i></i><i></i><i></i></div>

<section class="abs service" style="left:112px;top:740px;width:448px">
  <svg width="76" height="74" viewBox="0 0 76 74" fill="none" stroke="#fff" stroke-width="3" stroke-linecap="round" stroke-linejoin="round">
    <path d="M28 30V4M20 12l8-8 8 8M46 4v26M38 22l8 8 8-8"/>
    <path d="M2 70l14-14c6-5 14-4 20-2h14a4 4 0 0 1 0 8H34M50 62l16-10a5 5 0 0 1 6 7L52 72H22"/>
  </svg>
  <h2 style="margin-top:26px">Trading Service</h2>
  <p style="text-align:justify">Nemo enim ipsam voluptatem quia voluptas sit aspernatur aut odit aut fugit, sed quia consequuntur magni dolores eos qui ratione voluptatem sequi nesciunt.</p>
  <span class="btn-outline">Read More</span>
</section>

<section class="abs service" style="left:628px;top:756px;width:460px;text-align:right">
  <svg width="68" height="64" viewBox="0 0 68 64" fill="none" stroke="#fff" stroke-width="3" stroke-linecap="round" stroke-linejoin="round">
    <path d="M42 8V2H4v60h38V46"/><path d="M12 14h22M12 22h18M12 30h14M12 40h10"/><path d="M22 52c4-6 8 4 12-2"/>
    <path d="M62 6l4 4-26 28-8 3 3-8z"/>
  </svg>
  <h2 style="margin-top:20px">Contracting Service</h2>
  <p>Nemo enim ipsam voluptatem quia voluptas sit aspernatur aut odit aut fugit, sed quia consequuntur magni dolores eos qui ratione voluptatem sequi nesciunt.</p>
  <span class="btn-outline">Read More</span>
</section>

<section class="abs about">
  <div class="eyebrow">About</div>
  <h2>KVR Globalinks</h2>
  <p>Nemo enim ipsam voluptatem quia voluptas sit aspernatur aut odit aut fugit, sed quia consequuntur magni dolores eos qui ratione voluptatem sequi nesciunt. Neque porro quisquam est, qui dolorem ipsum quia dolor sit amet, consectetur, adipisci velit, sed quia non numquam eius modi tempora incidunt ut labore et dolore magnam aliquam quaerat voluptatem.</p>
  <span class="btn-dark">Read More</span>
</section>

<div class="abs offers-bg" role="img" aria-label="Faint sketch of a city skyline with buildings under construction"></div>
<svg class="abs" style="left:0;top:1500px" width="1200" height="740" viewBox="0 1500 1200 740">
  <polyline points="0,1625 600,1504 1200,1625" fill="none" stroke="#222" stroke-width="1.5"/>
  <polygon points="300,1565 600,1504 900,1565 900,1572 600,1512 300,1572" fill="#222"/>
  <polyline points="0,2118 600,2233 1200,2118" fill="none" stroke="#222" stroke-width="1.5"/>
  <polygon points="300,2176 600,2233 900,2176 900,2168 600,2225 300,2168" fill="#222"/>
</svg>
<h2 class="abs offers-title">COMPANY OFFERS</h2>
<div class="abs offers-rule"></div>

<svg class="abs" style="left:38px;top:1862px" width="24" height="44" viewBox="0 0 24 44" fill="none" stroke="#333" stroke-width="2.5"><path d="M22 2L2 22l20 20"/></svg>
<svg class="abs" style="left:1138px;top:1862px" width="24" height="44" viewBox="0 0 24 44" fill="none" stroke="#333" stroke-width="2.5"><path d="M2 2l20 20-20 20"/></svg>

<div class="abs tile cream" style="left:99px;top:1719px;width:190px;height:160px">
  <svg width="54" height="54" viewBox="0 0 54 54"><circle cx="27" cy="27" r="25" fill="none" stroke="#111" stroke-width="3"/><path d="M27 12c6 9 10 14 10 19a10 10 0 0 1-20 0c0-5 4-10 10-19z" fill="#111"/></svg>
  OIL
</div>
<div class="abs tile cream" style="left:99px;top:1892px;width:190px;height:159px">
  <svg width="54" height="54" viewBox="0 0 54 54" fill="none" stroke="#111" stroke-width="3"><path d="M40 10a22 22 0 1 0 6 12"/><path d="M30 14l-10 15h10l-6 12"/></svg>
  ENEGY AND GAS
</div>
<div class="abs feature">
  <svg width="94" height="94" viewBox="0 0 94 94" fill="none" stroke="#fff" stroke-width="4" stroke-linecap="round" stroke-linejoin="round" style="margin-top:34px">
    <path d="M20 54a27 27 0 0 1 54 0"/><path d="M14 54h66v8H14z"/><path d="M38 30v22M56 30v22M47 27v25"/>
    <path d="M70 14a10 10 0 0 1 12 12l-10-2-2 2z"/><path d="M64 32l-8 8"/>
    <path d="M30 70L10 88"/><circle cx="9" cy="89" r="3"/>
  </svg>
  <h3>CONSTRUCTION</h3>
  <p>Sed ut perspiciatis unde omnis iste natus<br>error sit voluptatem.</p>
</div>
<div class="abs tile cream" style="left:910px;top:1719px;width:190px;height:160px">
  <svg width="54" height="54" viewBox="0 0 54 54" fill="none" stroke="#111" stroke-width="2.5" stroke-linecap="round"><path d="M27 4v6M10 12l4 4M44 12l-4 4M4 27h6M44 27h6"/><path d="M8 30a19 19 0 0 0 38 0z"/><path d="M27 48V32M27 38c-6-2-9-6-9-10 5 0 9 4 9 10zM27 38c6-2 9-6 9-10-5 0-9 4-9 10z"/></svg>
  AGRICULTURE
</div>
<div class="abs tile green" style="left:910px;top:1892px;width:190px;height:159px">
  <svg width="52" height="52" viewBox="0 0 94 94" fill="none" stroke="#fff" stroke-width="5" stroke-linecap="round"><path d="M20 54a27 27 0 0 1 54 0M14 54h66v8H14zM38 30v22M56 30v22"/><path d="M70 14a10 10 0 0 1 12 12l-10-2-2 2zM30 70L10 88"/></svg>
  CONSTRUCTION
</div>

<article class="abs project" style="left:112px;background:var(--green)">
  <div class="project-photo" role="img" aria-label="Building site with concrete frame and scaffolding" style="background:linear-gradient(180deg,#b9c8d6 0%,#9a8f7e 45%,#6c5a48 100%)"></div>
  <div class="project-body">
    <h3>Civil contracting for infrastructure</h3>
    <p>Nemo enim ipsam voluptatem quia voluptas sit aspernatur aut odit aut fugit, sed quia consequuntur magni dolores.</p>
    <span class="btn-white" style="color:var(--green)">Read More</span>
  </div>
</article>
<article class="abs project" style="left:600px;background:var(--gold)">
  <div class="project-photo" role="img" aria-label="Modern white residential apartment building" style="background:linear-gradient(180deg,#7fa6d6 0%,#e9ecef 30%,#d8d4cc 75%,#9aa38a 100%)"></div>
  <div class="project-body">
    <h3>Residential and heavy projects</h3>
    <p>Nemo enim ipsam voluptatem quia voluptas sit aspernatur aut odit aut fugit, sed quia consequuntur magni dolores.</p>
    <span class="btn-white" style="color:var(--gold)">Read More</span>
  </div>
</article>

<div class="abs find-band"></div>
<svg class="abs" style="left:0;top:2786px" width="410" height="90" viewBox="0 0 410 90"><polygon points="0,0 408,0 358,90 0,90" fill="var(--green)"/></svg>
<h2 class="abs find-title">Find Your Service</h2>
<p class="abs find-text">Nemo enim ipsam voluptatem quia voluptas sit aspernatur aut odit aut fugit, sed quia consequuntur</p>
<span class="abs btn-gold">Search Now</span>

<footer class="abs site-footer"></footer>
<div class="abs footer-brand"><span class="brand-dot"></span>KVR GLOBALINKS</div>
<h2 class="abs footer-title">CONTACT US</h2>
<div class="abs contact-item" style="top:3034px">
  <span class="ring"><svg width="24" height="24" viewBox="0 0 24 24" fill="none" stroke="#fff" stroke-width="1.8"><path d="M5 3h4l2 5-3 2a11 11 0 0 0 6 6l2-3 5 2v4a2 2 0 0 1-2 2A17 17 0 0 1 3 5a2 2 0 0 1 2-2z"/></svg></span>
  +1 555 019 4432
</div>
<div class="abs contact-item" style="top:3094px">
  <span class="ring"><svg width="24" height="24" viewBox="0 0 24 24" fill="none" stroke="#fff" stroke-width="1.8"><rect x="3" y="9" width="18" height="12" rx="1"/><path d="M7 9V3h10v6M7 13h4M7 17h4M15 13h2M15 17h2"/></svg></span>
  (555) 014-2870
</div>
<div class="abs contact-item" style="top:3152px">
  <span class="ring"><svg width="24" height="24" viewBox="0 0 24 24" fill="none" stroke="#fff" stroke-width="1.8"><path d="M12 22s7-7 7-13a7 7 0 0 0-14 0c0 6 7 13 7 13z"/><circle cx="12" cy="9" r="2.5"/></svg></span>
  <span>1180 Harbor Way 210,<br>Lakeview, NV 123</span>
</div>
<p class="abs copyright">Copyrights @ 2020 KVR Globalinks. All Rights Reserved.</p>

</body>
</html>
```